KVM Contracting services . Building and maintenance services, optic fibre installation

Business cards and logo design.I need a logo that I can use on business cards ,workwear and on my vehicles. I would like the KVM to be the main or larger text and contracting services to be the smaller or less important text.I like monograms, modern designs and repeating patterns symbols. I am also a Gemini and my favourite number is 22 so if this can be any inspiration to help with the design. Am thinking of the using German flag colours as a his is my family’s heritage. And the other 2 main colours I wear is black and white.But any ideas are appreciated.I do not need a design that is trade specific but a design that could be used for any business.

Target Market(s)

General public

Contact Information for Business Card

KVM Contracting Services ( front of business card)

(Back of business card)
Darren Holtwick
0451907326
Maintenance services
Optic fibre and data installation

Logo Text

Logo can just be pattern or monogram or incorporate KVM . I like the gemini star sign and the number 22

Colors
ec1f27
000000
fbee3e
ffffff

Requirements
Must have
• Logo and KVM Contracting Services on the front of business card
Nice to have
• Possible use of German flag colours.
• Modern design.
• Design to be able to be used on black or white background as I want to put it on clothing

```html
<!DOCTYPE html>
<html lang="en">
<head>
<meta charset="utf-8">
<title>KVM Contracting Services – Business Card</title>
<link rel="stylesheet" href="https://fonts.googleapis.com/css2?family=Roboto:wght@500;700&family=Open+Sans:wght@400&display=swap">
<style>
  :root {
    --page-bg: #e9e6e2;
    --card-top: #1c0c0c;
    --card-dark-red: #7a0608;
    --card-red: #f20c0c;
    --card-orange: #ff6a00;
    --card-amber: #ffb400;
    --ink-light: #ffffff;
    --badge-fill: #efefef;
    --logo-ink: #1b1b1b;
  }
  * { box-sizing: border-box; margin: 0; padding: 0; }
  html, body {
    width: 1200px;
    height: 900px;
    overflow: hidden;
    background: var(--page-bg);
  }
  .business-card {
    position: absolute;
    left: 120px;
    top: 153px;
    width: 960px;
    height: 594px;
    overflow: hidden;
    background: linear-gradient(180deg,
      var(--card-top) 0%,
      var(--card-dark-red) 22%,
      var(--card-red) 48%,
      var(--card-orange) 78%,
      var(--card-amber) 100%);
    box-shadow: 0 12px 30px rgba(0,0,0,0.18);
  }
  .holder-name {
    position: absolute;
    left: 54px;
    top: 70px;
    font-family: "Roboto", sans-serif;
    font-weight: 700;
    font-size: 33px;
    letter-spacing: 0.3px;
    color: var(--ink-light);
  }
  .holder-phone {
    position: absolute;
    left: 54px;
    top: 118px;
    font-family: "Open Sans", sans-serif;
    font-size: 26px;
    color: var(--ink-light);
  }
  .service-list {
    position: absolute;
    left: 56px;
    top: 424px;
    list-style: none;
    font-family: "Open Sans", sans-serif;
    font-size: 26px;
    line-height: 34px;
    color: var(--ink-light);
  }
  .brand-badge {
    position: absolute;
    left: 421px;
    top: 37px;
    width: 514px;
    height: 514px;
    border-radius: 50%;
    background: var(--badge-fill);
    display: flex;
    flex-direction: column;
    align-items: center;
    justify-content: center;
  }
  .brand-name {
    font-family: "Roboto", sans-serif;
    font-weight: 700;
    color: var(--logo-ink);
    text-align: center;
    line-height: 1;
  }
  .brand-name .brand-initials {
    display: block;
    font-size: 120px;
    letter-spacing: 4px;
  }
  .brand-name .brand-descriptor {
    display: block;
    margin-top: 10px;
    font-size: 30px;
    letter-spacing: 1px;
  }
</style>
</head>
<body>
  <article class="business-card">
    <h1 class="holder-name">DARREN HOLTWICK</h1>
    <p class="holder-phone">0451907326</p>
    <ul class="service-list">
      <li>Maintenance services</li>
      <li>Optic fibre and data installation</li>
    </ul>
    <div class="brand-badge">
      <p class="brand-name">
        <span class="brand-initials">KVM</span>
        <span class="brand-descriptor">CONTRACTING SERVICES</span>
      </p>
    </div>
  </article>
</body>
</html>
```